Design a product box

I need a product box designed for my brand "ClikaDot" I have attached logo and a rough design example. You don't have to follow the design so you can create other concepts.
Colours to follow: Baby pink, baby blue, purple and white.
The lid is going to be magnetic once the flap closes down.
Inside the box there will be a product insert tray which will be made of foam EVA where the product will sit on.
Camera size: 115*64*34mm
Box size: 140*120*90mm
DETAILS ON THE BOX BELOW:
Top of box
"CLIKADOT
"
"Reusable Film Camera"
-----------------
Where ever that is visually is best, to have colour options displayed in check boxes.
Colour:
White
Blue
Peach
Purple
-----------------
Back of box
- Barcode (Can you create a barcode that is functional)
Package Contents
1 x ClikaDot Reusable Film Camera
1 x Lanyard
Battery not included. 1 x AAA Required.
Company logo with website included/
www.clikadot.com.au
-----------------
Inside of box lid
Say hello to unforgettable memories and goodbye to single use.
(Logo on bottom, centred in the the middle)
Target Market(s)
Majority young females
Industry/Entity Type
Selling film cameras, retro, young and cool

```html
<!DOCTYPE html>
<html lang="en">
<head>
<meta charset="utf-8">
<title>ClikaDot – Product Box Dieline</title>
<link rel="stylesheet" href="https://fonts.googleapis.com/css2?family=Quicksand:wght@600;700&family=Open+Sans:wght@400;600;700&family=Ubuntu+Mono&display=swap">
<style>
  :root {
    --page: #e9d8f1;
    --brand-soft: #dcb2ee;
    --lid: #ddb8f3;
    --white: #ffffff;
    --blue: #3a36f5;
    --purple: #b657d8;
    --mint: #b6f0ec;
    --footer: #dcc2ee;
    --shadow: rgba(90, 50, 120, 0.35);
  }
  * { margin: 0; padding: 0; box-sizing: border-box; }
  html, body { width: 849px; height: 1200px; overflow: hidden; background: var(--page); }
  .canvas { position: relative; width: 849px; height: 1200px; font-family: "Open Sans", sans-serif; color: var(--white); }

  .brand-header { position: absolute; left: 0; top: 58px; width: 100%; display: flex; flex-direction: column; align-items: center; gap: 14px; }
  .brand-mark { width: 36px; height: 22px; border-radius: 4px; background: var(--brand-soft); }
  .brand-name { font-family: "Quicksand", sans-serif; font-weight: 700; font-size: 44px; color: var(--brand-soft); letter-spacing: -0.5px; line-height: 1; }

  .dieline { position: absolute; width: 549px; height: 434px; filter: drop-shadow(4px 6px 4px var(--shadow)); }
  .dieline--lid { left: 80px; top: 222px; }
  .dieline--outer { left: 221px; top: 556px; }
  .dieline svg { display: block; }

  .panel-text { position: absolute; display: flex; flex-direction: column; align-items: center; text-align: center; }
  .logo-word { font-family: "Quicksand", sans-serif; font-weight: 700; line-height: 1; }
  .tagline { font-weight: 600; line-height: 1; }
  .web { font-weight: 600; line-height: 1; }

  .lid-message { left: 234px; top: 266px; width: 240px; }
  .lid-message .hello { font-size: 14px; font-weight: 600; }
  .lid-message .hello b { font-weight: 700; }
  .lid-message .line { font-size: 8.5px; font-weight: 600; margin-top: 4px; }
  .lid-message .logo-word { font-size: 14px; margin-top: 30px; }
  .lid-message .tagline { font-size: 5.5px; margin-top: 3px; }

  .back-panel { left: 375px; top: 556px; width: 240px; height: 152px; transform: rotate(180deg); padding-top: 36px; }
  .back-panel .heading { font-size: 5.5px; font-weight: 700; }
  .back-panel .content { font-size: 5px; margin-top: 5px; line-height: 1.9; }
  .colour-options { display: flex; gap: 10px; margin-top: 10px; font-size: 5px; }
  .colour-options span { display: flex; align-items: center; gap: 3px; }
  .colour-options i { width: 8px; height: 8px; border: 1px solid var(--white); }

  .front-panel { left: 375px; top: 778px; width: 240px; }
  .front-panel .logo-word { font-size: 22px; }
  .front-panel .tagline { font-size: 9px; margin-top: 6px; }
  .front-panel .web { font-size: 5.5px; margin-top: 38px; }

  .side-panel { width: 205px; transform: translate(-50%, -50%); }
  .side-panel .logo-word { font-size: 20px; }
  .side-panel .tagline { font-size: 6.5px; margin-top: 5px; }
  .side-panel .web { font-size: 5px; margin-top: 30px; }
  .side-panel--left { left: 290px; top: 811px; transform: translate(-50%, -50%) rotate(90deg); }
  .side-panel--right { left: 698px; top: 811px; transform: translate(-50%, -50%) rotate(-90deg); }

  .palette { position: absolute; top: 1065px; left: 0; width: 100%; display: flex; justify-content: center; gap: 32px; }
  .palette i { width: 21px; height: 21px; }
  .palette .swatch-blue { background: var(--blue); }
  .palette .swatch-purple { background: var(--purple); }
  .palette .swatch-mint { background: var(--mint); }

  .specs { position: absolute; top: 1140px; width: 100%; text-align: center; font-family: "Ubuntu Mono", monospace; font-size: 15px; letter-spacing: 1.5px; color: var(--footer); }
</style>
</head>
<body>
<main class="canvas">

  <header class="brand-header">
    <span class="brand-mark"></span>
    <span class="brand-name">ClikaDot</span>
  </header>

  <!-- inside lid dieline -->
  <div class="dieline dieline--lid">
    <svg width="549" height="434" viewBox="0 0 549 434">
      <path d="M154 0H394V151H549V357H394V434H154V357H0V151H154Z" fill="var(--lid)"/>
      <g stroke="var(--white)" stroke-width="1" stroke-dasharray="4 3" fill="none" opacity="0.85">
        <path d="M154 151H394M154 357H394M154 151V357M394 151V357"/>
      </g>
    </svg>
  </div>

  <div class="panel-text lid-message">
    <p class="hello">Say <b>HELLO</b></p>
    <p class="line">to unforgettable memories and</p>
    <p class="line">goodbye to single use.</p>
    <p class="logo-word">ClikaDot</p>
    <p class="tagline">Reusable Film Camera</p>
  </div>

  <!-- outer box dieline -->
  <div class="dieline dieline--outer">
    <svg width="549" height="434" viewBox="0 0 549 434">
      <defs>
        <linearGradient id="boxGradient" gradientUnits="userSpaceOnUse" x1="0" y1="434" x2="549" y2="0">
          <stop offset="0" stop-color="#b6f0ec"/>
          <stop offset="0.3" stop-color="#b9a9e8"/>
          <stop offset="0.55" stop-color="#b85fdc"/>
          <stop offset="0.78" stop-color="#8048e8"/>
          <stop offset="1" stop-color="#3a36f5"/>
        </linearGradient>
      </defs>
      <path d="M154 0H394V152H549V357H394V434H154V357H0V152H154Z" fill="url(#boxGradient)"/>
      <g stroke="var(--white)" stroke-width="1" stroke-dasharray="4 3" fill="none" opacity="0.85">
        <path d="M154 152H394M154 357H394M154 152V357M394 152V357"/>
      </g>
    </svg>
  </div>

  <div class="panel-text back-panel">
    <p class="heading">Package Contents</p>
    <p class="content">• 1 x ClikaDot Reusable Film Camera • 1 x Lanyard<br>• Battery not included • 1 x AAA required.</p>
    <div class="colour-options">
      <span><i></i>white</span>
      <span><i></i>blue</span>
      <span><i></i>peach</span>
      <span><i></i>purple</span>
    </div>
  </div>

  <div class="panel-text front-panel">
    <p class="logo-word">ClikaDot</p>
    <p class="tagline">Reusable Film Camera</p>
    <p class="web">www.clikadot.com.au</p>
  </div>

  <div class="panel-text side-panel side-panel--left">
    <p class="logo-word">ClikaDot</p>
    <p class="tagline">Reusable Film Camera</p>
    <p class="web">www.clikadot.com.au</p>
  </div>

  <div class="panel-text side-panel side-panel--right">
    <p class="logo-word">ClikaDot</p>
    <p class="tagline">Reusable Film Camera</p>
    <p class="web">www.clikadot.com.au</p>
  </div>

  <div class="palette">
    <i class="swatch-blue"></i>
    <i class="swatch-purple"></i>
    <i class="swatch-mint"></i>
  </div>

  <p class="specs">camera size : 115x64x34mm &nbsp;•&nbsp; box size : 140x120x90mm</p>

</main>
</body>
</html>
```